Web site for radio show

I've got a radio show starting on OrbitalWave and need a web site for it. I am familiar with WordPress, so I'd like to get a design for a WordPress-based web site for the show.

I'm also posting a logo project to be done at the same time.

The best radio show web site I've seen is the Cosmic Tuesday site (www.cosmictuesday-example.com). That's a good model but I don't want to start with that much complexity and content. The initial site that I'd like you to design would have the following parts:
- Upcoming shows
- Past shows (including links to authors, their web sites, and their books)
- Chirp feed
- Blog
- About
- ...and anything else you think would be necessary

For colors, I'd like it to be consistent with my personal web site: www.kellaway-ventures-example.com

Target Market(s)

The target market for this show is mid- to upper-level managers

Industry/Entity Type

Radio

Requirements
Must have
• The project has to proceed in (at least) two stages: a first rough layout, and a second finished design. Whether you want a third stage in between with look and feel options is up to you.

```html
<!DOCTYPE html>
<html lang="en">
<head>
<meta charset="utf-8">
<title>Kellaway Show</title>
<link href="https://fonts.googleapis.com/css2?family=Roboto+Condensed:wght@400;700&family=Roboto:wght@400;500&family=Open+Sans:wght@400&display=swap" rel="stylesheet">
<style>
:root{
  --red:#d3202b;
  --ink:#333333;
  --grey:#8a8a8a;
  --light:#f2f2f2;
  --line:#e3e3e3;
  --black:#050505;
  --white:#ffffff;
}
*{box-sizing:border-box;margin:0;padding:0}
html,body{width:994px;height:1200px;overflow:hidden;background:var(--white)}
body{font-family:"Roboto",Arial,sans-serif;color:var(--ink);position:relative}
.abs{position:absolute}
.brand{left:108px;top:12px;font-family:"Roboto Condensed",sans-serif;font-weight:700;font-size:33px;color:var(--ink);letter-spacing:-0.5px;transform:scaleY(1.05)}
.phone{left:490px;top:14px;font-size:18px;color:var(--ink);display:flex;align-items:center;gap:6px}
.phone .area{color:var(--red)}
.like{left:691px;top:20px;display:flex;align-items:center;gap:3px;font-size:9px}
.like .btn{background:#4a66a0;color:#fff;padding:2px 5px;border-radius:2px;font-weight:500}
.like .count{border:1px solid #bbb;padding:1px 3px;color:#555}
.social{left:770px;top:15px;display:flex;gap:7px}
.social span{width:25px;height:25px;border-radius:50%;background:#c9c9c9;display:block}
.nav{left:0;top:55px;width:994px;height:35px;border-top:1px solid var(--line);border-bottom:3px solid var(--red)}
.nav ul{position:absolute;left:108px;top:0;display:flex;list-style:none;height:32px}
.nav li{font-family:"Roboto Condensed",sans-serif;font-size:13.5px;padding:0 14px;line-height:32px;border-left:1px solid var(--line)}
.nav li:last-child{border-right:1px solid var(--line)}
.nav li.active{color:var(--red);position:relative}
.nav li.active:after{content:"";position:absolute;left:50%;bottom:0;margin-left:-4px;border:4px solid transparent;border-bottom-color:var(--red)}
.nav .search{position:absolute;left:855px;top:0;width:30px;height:32px;border-left:1px solid var(--line);display:flex;align-items:center;justify-content:center}
.hero{left:109px;top:107px;width:776px;height:301px;background:var(--black)}
.hero .photo{position:absolute;left:0;top:0;width:310px;height:301px;background:radial-gradient(ellipse at 45% 40%,#b08c78 0%,#6a4a3a 45%,#1a1310 85%)}
.hero h1{position:absolute;left:280px;top:114px;font-family:"Roboto Condensed",sans-serif;font-weight:400;font-size:21.5px;color:#fff;white-space:nowrap}
.hero p{position:absolute;left:298px;top:165px;width:470px;font-size:8.8px;line-height:19.5px;color:#fff}
.dots{position:absolute;left:487px;top:233px;display:flex;gap:4px}
.dots i{width:7px;height:7px;border-radius:50%;background:#fff;display:block}
.dots i.on{background:var(--red)}
.bar{height:27px;background:var(--light);border-bottom:1px solid var(--line);font-size:13px;line-height:27px;padding-left:17px}
.bar .go{position:absolute;right:14px;top:6px}
.blog-bar{left:109px;top:430px;width:457px}
.post{top:473px;width:206px}
.post .img{height:132px}
.post h3{font-weight:400;font-size:11px;color:var(--red);margin-top:10px}
.post p{font-size:8.6px;color:var(--grey);line-height:17px;margin-top:9px}
.share{display:inline-flex;align-items:center;gap:2px;margin-top:6px;font-size:8px}
.share b{border:1px solid #bbb;border-radius:2px;padding:1px 4px;background:#f6f6f6;font-weight:500;color:#224}
.share span{border:1px solid #bbb;padding:1px 3px}
.card{left:596px;width:291px;background:var(--light);border:1px solid #ececec}
.card .thumb{position:absolute;left:14px;top:17px;width:84px}
.card h4{position:absolute;left:105px;top:15px;font-weight:400;font-size:12.5px}
.card .mini{position:absolute;right:14px;top:18px;display:flex;gap:3px}
.card .mini i{width:6px;height:6px;border-radius:50%;background:#d0d0d0;display:block}
.card .mini i.on{background:var(--red)}
.card p{position:absolute;left:105px;top:36px;width:175px;font-size:8.6px;color:var(--grey);line-height:17px}
.card .more{position:absolute;left:14px;width:264px;display:flex;align-items:center;font-size:9.5px;color:var(--ink)}
.card .more .rule{flex:1;height:1px;background:var(--red);position:relative;margin-right:6px}
.card .more .rule:after{content:"";position:absolute;right:-3px;top:-3px;border:3px solid transparent;border-left-color:var(--red)}
.card h5{position:absolute;left:15px;top:94px;font-weight:400;font-size:14px;color:var(--red)}
.past-bar{left:109px;top:733px;width:457px}
.book{left:108px;top:782px;width:144px;height:202px;background:linear-gradient(160deg,#ffffff 0%,#eef2f4 55%,#d9dde0 100%);border:1px solid #d2d2d2;box-shadow:6px 10px 14px rgba(0,0,0,.12)}
.book-text{left:261px;top:789px;width:307px;font-size:10.8px;line-height:19.3px;color:var(--grey)}
.book-text a{color:var(--red);text-decoration:none;font-size:10.5px}
.tile{top:925px;height:67px;color:#fff;font-family:"Roboto Condensed",sans-serif;font-size:17px;display:flex;align-items:center;justify-content:center}
.about{left:595px;top:734px;width:290px;height:259px;background:var(--black);color:#fff}
.about h2{position:absolute;left:29px;top:22px;font-weight:400;font-size:20.5px;white-space:nowrap}
.about .lead{position:absolute;left:31px;top:62px;width:252px;font-family:"Open Sans",sans-serif;font-size:8.6px;line-height:19.5px}
.about .photo{position:absolute;left:0;top:118px;width:140px;height:141px;background:radial-gradient(ellipse at 45% 35%,#b08c78 0%,#6b4a38 45%,#0a0706 85%)}
.about .quote{position:absolute;left:114px;top:130px;width:170px;font-family:"Open Sans",sans-serif;font-size:8.6px;line-height:19.5px}
.about .btn{position:absolute;left:157px;top:209px;width:100px;height:26px;background:var(--red);font-size:12px;line-height:26px;text-align:center}
.testimonial{left:108px;top:1024px;width:60px;height:53px}
.testimonial-text{left:188px;top:1030px;width:700px;font-family:"Open Sans",sans-serif;font-size:8.8px;line-height:21.5px;color:var(--ink)}
.mark{font-family:Georgia,serif;font-size:22px;color:#a88c5a;line-height:0;font-weight:700}
.footer{left:0;top:1111px;width:994px;height:89px;border-top:1px solid var(--line)}
.footer .network{position:absolute;left:108px;top:28px;font-family:"Roboto",sans-serif;font-weight:500;font-size:27px;color:#1f5a9a;display:flex;align-items:center;gap:8px}
.footer .network i{width:14px;height:14px;border-radius:50%;background:#1f5a9a;display:block}
.footer ul{position:absolute;right:108px;top:26px;display:flex;gap:10px;list-style:none;font-size:12.5px}
.footer small{position:absolute;right:110px;top:53px;font-size:8.8px;letter-spacing:.2px}
</style>
</head>
<body>

<header>
  <div class="abs brand">KELLAWAY SHOW</div>
  <div class="abs phone">
    <svg width="13" height="13" viewBox="0 0 24 24"><path fill="#8a8a8a" d="M6.6 10.8c1.4 2.8 3.8 5.1 6.6 6.6l2.2-2.2c.3-.3.7-.4 1-.2 1.1.4 2.3.6 3.6.6.6 0 1 .4 1 1V20c0 .6-.4 1-1 1C10.6 21 3 13.4 3 4c0-.6.4-1 1-1h3.5c.6 0 1 .4 1 1 0 1.3.2 2.5.6 3.6.1.3 0 .7-.2 1L6.6 10.8z"/></svg>
    <span><span class="area">( 555 )</span>-010-4821</span>
  </div>
  <div class="abs like"><span class="btn">Like</span><span class="count">37k</span></div>
  <div class="abs social"><span></span><span></span><span></span><span></span></div>
</header>

<nav class="abs nav">
  <ul>
    <li class="active">HOME</li>
    <li>UPCOMING SHOWS</li>
    <li>PAST SHOWS</li>
    <li>BLOG</li>
    <li>NEWS</li>
    <li>CONTACT US</li>
  </ul>
  <div class="search">
    <svg width="14" height="14" viewBox="0 0 16 16"><circle cx="6" cy="6" r="4.2" fill="none" stroke="#444" stroke-width="1.8"/><path d="M9.2 9.2L14 14" stroke="#444" stroke-width="2.2"/></svg>
  </div>
</nav>

<section class="abs hero">
  <div class="photo" role="img" aria-label="Portrait of Daniel Kellaway speaking with a headset microphone"></div>
  <h1>Hear Daniel Speak Keynotes, Conferences, Small Groups..</h1>
  <p>Lorem ipsum dolor sit amet, consectetur adipiscing elit. Nunc sed lacus mollis, fermentum risus et, porta erat. Nulla nec varius orci, at eleifend risus. Interdum et malesuada fames ac ante ipsum primis in faucibus. Nam mattis ullamcorper sem, elementum iaculis mi eleifend ac. Donec id molestie magna...</p>
  <div class="dots"><i></i><i class="on"></i><i></i><i></i></div>
</section>

<div class="abs bar blog-bar">Our Latest Blog
  <svg class="go" width="14" height="14" viewBox="0 0 14 14"><circle cx="7" cy="7" r="7" fill="#d3202b"/><path d="M5.5 4l3 3-3 3" fill="none" stroke="#fff" stroke-width="1.6"/></svg>
</div>

<article class="abs post" style="left:109px">
  <div class="img" role="img" aria-label="Group photo of guests at an evening event" style="background:linear-gradient(180deg,#4a3a30,#2a2420 60%,#3a4a6a)"></div>
  <h3>Post Opened by Default</h3>
  <p>Donec ante felis, sollicitudin aghghc leffo non, c ursus faucibus augue. Aeneagjfgdfhhgn sceleris imperdiet diam a.</p>
  <div class="share"><b>Share</b><span>1</span></div>
</article>

<article class="abs post" style="left:361px">
  <div class="img" role="img" aria-label="Guests shaking hands at a formal reception" style="background:linear-gradient(180deg,#8a7a6a,#3a3230 55%,#1a1a1e)"></div>
  <h3>Post Opened by Default</h3>
  <p>Donec ante felis, sollicitudin aghghc leffo non, c ursus faucibus augue. Aeneagjfgdfhhgn sceleris imperdiet diam a.</p>
  <div class="share"><b>Share</b><span>1</span></div>
</article>

<aside class="abs card" style="top:431px;height:138px">
  <div class="thumb" role="img" aria-label="Guest speaker on stage" style="height:64px;background:linear-gradient(90deg,#5a4a40,#8aa8c8)"></div>
  <h4>Upcoming Shows</h4>
  <div class="mini"><i></i><i class="on"></i><i></i><i></i></div>
  <p>website states, "It's a fundamental questi on that spans the sciences. It can be ans wered from the perspective...............</p>
  <h5>Rebuilding Bricko</h5>
  <div class="more" style="top:114px"><span class="rule"></span>Read More</div>
</aside>

<aside class="abs card" style="top:592px;height:118px">
  <div class="thumb" role="img" aria-label="Guest standing in front of wooden barrels" style="height:64px;background:linear-gradient(90deg,#7a5030,#2a3a5a)"></div>
  <h4>Chirp Feeds</h4>
  <div class="mini"><i></i><i class="on"></i><i></i><i></i></div>
  <p>"website states, "It's a fundamental questi on that spans the sciences. It can be ans wered from the perspecti "</p>
  <div class="more" style="top:93px"><span class="rule"></span>Read More</div>
</aside>

<div class="abs bar past-bar">Our Past Shows
  <svg class="go" width="14" height="14" viewBox="0 0 14 14"><circle cx="7" cy="7" r="7" fill="#d3202b"/><path d="M5.5 4l3 3-3 3" fill="none" stroke="#fff" stroke-width="1.6"/></svg>
</div>

<div class="abs book" role="img" aria-label="Cover of the book Block by Block by Daniel Kellaway"></div>
<p class="abs book-text">A fascinating book. The story of how Bricko came perilously clo se to disaster but then transformed itself into one of the most successful and innovative companies in the world serves both as an inspiration and an object lesson."-Marcus Hale, former Editor-in-Chief of Circuit and author of Builders and The <a href="#">http://www.kellaway-ventures-example.com/#sthash.tH2T8Qti.dpuf</a></p>

<div class="abs tile" style="left:265px;width:137px;background:linear-gradient(90deg,#3e4a58,#6a8aa0)" role="img" aria-label="Author portrait">AUTHORS</div>
<div class="abs tile" style="left:430px;width:136px;background:linear-gradient(90deg,#b89a40,#3a4a6a)" role="img" aria-label="Collage of guest web pages">WEB SITES</div>

<section class="abs about">
  <h2>About Kellaway Show!</h2>
  <p class="lead">Lorem ipsum dolor sit amet, consectetur adipisicing elit, or incididunt ut labore et dolore magna aliqua. Ut enim nostrud exercitation ullamco laboris nisi ut aliquip ex ea</p>
  <div class="photo" role="img" aria-label="Daniel Kellaway speaking at an event"></div>
  <p class="quote">Duis aute irure dolor in reprehende Excepteur sint occaecat cupidatat n erunt mollit anim id est laborum."</p>
  <div class="btn">Read More</div>
</section>

<svg class="abs testimonial" viewBox="0 0 60 53" role="img" aria-label="Listener portrait in a hexagon frame">
  <polygon points="15,1 45,1 59,26.5 45,52 15,52 1,26.5" fill="#3a3a3a"/>
  <polygon points="16,4 44,4 56,26.5 44,49 16,49 4,26.5" fill="#b58a62"/>
</svg>
<p class="abs testimonial-text"><span class="mark">&ldquo;</span>Claritas est etiam processus dynamicus, qui sequitur mutationem consuetudium lectorum.Mirum est notare quam littera gothica, Claritas est etiam processus dy qui sequitur mutationem mutationem mutationem consuetudium lectorum.Mirum est notare quam futurum........................ <span class="mark">&rdquo;</span></p>

<footer class="abs footer">
  <div class="network"><i></i>OrbitalWave</div>
  <ul><li>Contact</li><li>Supporters</li><li>Newsletter</li><li>Policies</li><li>Available from PodStream</li></ul>
  <small>COPYRIGHT DANIEL KELLAWAY 2014.</small>
</footer>

</body>
</html>
```